Brisbane IT support business needs our first website

Hi All,

We are after a new website design for our IT solutions and support business.The business name is Harbourline Computing Services Group, or HCSG for short. We provide a range of solutions and services within the IT space.

I would like to utilize the two colours in our business logo I have uploaded.

I understand this is initially for the design only aspect of the site, but I would like to engage the winner to finish coding the website and finalize after also.

Target Market(s)

Other businesses owners and home users.

Industry/Entity Type

Business

Requirements
Must have
• Nice clean and functional design utilizing our business colours from the logo.

```html
<!DOCTYPE html>
<html lang="en">
<head>
<meta charset="utf-8">
<title>HCSG – IT Solutions</title>
<link href="https://fonts.googleapis.com/css2?family=Oswald:wght@300;400;500&family=Open+Sans:wght@400;600;700&display=swap" rel="stylesheet">
<style>
:root{
  --navy:#0d4a66;
  --orange:#f07e1f;
  --ink:#333;
  --muted:#666;
  --light:#f4f4f4;
  --lighter:#efefef;
  --footer:#232323;
  --footer-deep:#1a1a1a;
  --field:#141414;
}
*{margin:0;padding:0;box-sizing:border-box}
html,body{width:1200px;height:2362px;overflow:hidden}
body{font-family:"Open Sans",Arial,sans-serif;color:var(--ink);background:#fff;position:relative}
.wrap{position:relative;width:937px;margin:0 auto}
.site-header{height:129px;background:#fff}
.brand{position:absolute;left:0;top:24px;display:flex;align-items:center;gap:14px}
.brand-dot{width:72px;height:72px;border-radius:50%;background:var(--navy)}
.brand-text{border-left:3px solid var(--orange);padding-left:10px}
.brand-name{font-family:"Oswald",sans-serif;font-weight:500;font-size:36px;color:var(--orange);line-height:1}
.brand-sub{font-family:"Oswald",sans-serif;font-weight:500;font-size:9px;color:var(--orange);line-height:1.2;width:118px}
.main-nav{position:absolute;right:0;top:47px;display:flex;gap:8px}
.main-nav a{font-size:13px;color:#222;text-decoration:none;padding:7px 15px}
.main-nav a.active{background:var(--navy);color:#fff}
.hero{position:relative;height:556px;background:linear-gradient(100deg,#c9d6e2 0%,#e8eef3 35%,#9aa7b3 60%,#2d3540 85%,#6b7078 100%)}
.hero-caption{position:absolute;left:128px;top:123px;width:486px;height:302px;background:rgba(60,60,60,.75);padding:38px 26px;color:#fff}
.hero-caption h1{font-family:"Oswald",sans-serif;font-weight:400;font-size:82px;line-height:1}
.hero-caption h2{font-family:"Oswald",sans-serif;font-weight:400;font-size:29px;margin-top:14px}
.hero-caption p{font-family:"Oswald",sans-serif;font-weight:300;font-size:13px;line-height:1.7;margin-top:24px;text-transform:uppercase}
.hero-dots{position:absolute;left:131px;top:519px;display:flex;gap:9px}
.hero-dots span{width:17px;height:17px;border-radius:50%;background:#333}
.hero-dots span.on{background:var(--orange)}
.section-title{font-family:"Oswald",sans-serif;font-weight:400;font-size:25px;color:var(--orange);text-align:center}
.welcome{height:244px;padding-top:36px}
.welcome .lead{font-size:13.5px;font-weight:700;text-align:center;line-height:1.6;margin-top:18px;color:#333}
.welcome .body{font-size:12.2px;line-height:1.85;text-align:center;margin-top:10px;color:#555}
.services{height:341px;background:var(--light);padding-top:20px}
.service-grid{display:grid;grid-template-columns:326px 312px 299px;row-gap:84px;margin-top:30px}
.service{display:flex;gap:10px}
.service-icon{width:62px;height:62px;border-radius:50%;background:var(--navy);flex:none;display:flex;align-items:center;justify-content:center}
.service h3{font-family:"Oswald",sans-serif;font-weight:400;font-size:16px;color:#222;text-transform:uppercase}
.service p{font-size:12px;color:#555;line-height:1.75;margin-top:2px}
.read-more{font-family:"Oswald",sans-serif;font-size:11px;color:var(--orange);display:block;margin-top:2px}
.works{height:379px;background:var(--lighter);padding-top:24px}
.work-grid{display:grid;grid-template-columns:repeat(4,218px);justify-content:space-between;margin-top:24px}
.work-thumb{height:137px}
.work h3{font-family:"Oswald",sans-serif;font-weight:400;font-size:14px;color:#222;margin-top:20px}
.work p{font-size:11.5px;color:#555;line-height:1.6;margin-top:6px}
.btn-more{display:inline-block;background:#555;color:#fff;font-size:12px;padding:7px 15px;margin-top:14px}
.testimonials{height:310px;padding-top:36px}
.quote-row{display:flex;gap:9px;margin-top:20px}
.quote{width:464px;height:178px;border:1px solid #ddd;padding:18px 20px 0 60px;position:relative}
.quote-mark{position:absolute;left:20px;top:8px;font-family:Georgia,serif;font-size:56px;color:#bbb;line-height:1}
.quote p{font-size:12px;line-height:1.9;color:#555}
.author{display:flex;align-items:center;gap:12px;margin-top:14px}
.author-photo{width:50px;height:50px;border-radius:50%;background:linear-gradient(#c9c4bf,#8a8480);border:2px solid #ddd}
.author-name{font-size:12.5px;color:var(--orange);text-transform:uppercase;line-height:1.3}
.author-co{font-size:12.5px;color:#333;text-transform:uppercase}
.site-footer{height:325px;background:var(--footer);padding-top:66px}
.footer-cols{position:relative;height:259px}
.fcol{position:absolute;top:0}
.fcol h4{font-size:16px;font-weight:400;color:#ddd;text-transform:uppercase;margin-bottom:26px}
.fcol ul{list-style:none}
.fcol li{font-size:13px;color:#bbb;line-height:22px}
.links-two{display:flex;gap:48px}
.field{width:192px;height:39px;background:var(--field);margin-bottom:7px;font-size:12px;color:#777;padding:10px}
.field.msg{height:76px}
.submit{display:inline-block;background:var(--orange);color:#fff;font-size:12px;font-weight:700;padding:6px 10px;margin-top:3px}
.bottom-bar{height:78px;background:var(--footer-deep)}
.bottom-bar .wrap{display:flex;align-items:center;justify-content:space-between;height:78px}
.copy{font-size:12px;color:#ddd}
.social{display:flex;gap:24px;margin-right:60px}
.social span{width:12px;height:12px;border-radius:50%;background:#ddd}
</style>
</head>
<body>
<header class="site-header">
  <div class="wrap">
    <div class="brand">
      <div class="brand-dot"></div>
      <div class="brand-text">
        <div class="brand-name">HCSG</div>
        <div class="brand-sub">HARBOURLINE COMPUTING SERVICES GROUP</div>
      </div>
    </div>
    <nav class="main-nav">
      <a class="active">HOME</a><a>ABOUT</a><a>SERVICES</a><a>PROJECTS</a><a>BLOG</a><a>CONTACTS</a>
    </nav>
  </div>
</header>

<section class="hero" role="img" aria-label="Photo of business colleagues smiling in a meeting in a bright office">
  <div class="hero-caption">
    <h1>IT SOLUTIONS</h1>
    <h2>TO DELIVER BUSINESS VALUE!</h2>
    <p>Phasellus porta. Fusce suscipit varius mi. Cum sociis natoque penatibus et dis parturient montes, nascetur ridiculus mus. Nulla dui.</p>
  </div>
  <div class="hero-dots"><span></span><span class="on"></span><span></span></div>
</section>

<section class="welcome">
  <div class="wrap">
    <h2 class="section-title">Welcome to HCSG</h2>
    <p class="lead">LOREM IPSUM DOLOR SIT AMET, FALLI TOLLIT CETERO TE EOS. EA ULLUM LIBER APERIRI MI, IMPETUS ATE PHILOSOPHIA AD DUO, QUEM REGIONE NE IUS. VIS QUIS LOBORTIS DISSENTIAS EX, IN DU AFT PHILOSOPHIA, MALIS NECESSITATIBUS NO MEI.</p>
    <p class="body">Lorem ipsum dolor sit amet, falli tollit cetero te eos. Ea ullum liber aperiri mi, impetus ate philosophia ad duo, quem regione ne ius. Vis quis lobortis dissentias ex, in du aft philosophia, malis necessitatibus no mei. Volumus sensibus qui ex, eum duis doming ad. Modo liberavisse eu mel, no viris prompta sit. Pro labore sadipscing et. Ne peax egat usu te mel vivendo scriptorem. Pro labore sadipscing et. Ne pertinax egat usu te mel vivendo scriptorem.Cum ut tractatos imperdiet, no tamquam facilisi qui. Eum tibique consectetuer in, an referrentur vis, vocent deseruisse ex mel. Sed te idque graecis. Vel ne libris dolores, mel graece mel vivendo scriptorem.</p>
  </div>
</section>

<section class="services">
  <div class="wrap">
    <h2 class="section-title">Our Services</h2>
    <div class="service-grid">
      <div class="service">
        <div class="service-icon"><svg width="32" height="32" viewBox="0 0 32 32" fill="#fff"><circle cx="16" cy="16" r="4"/><circle cx="6" cy="6" r="4"/><circle cx="26" cy="6" r="4"/><circle cx="6" cy="26" r="4"/><circle cx="26" cy="26" r="4"/><path d="M6 6L26 26M26 6L6 26" stroke="#fff" stroke-width="2"/></svg></div>
        <div><h3>IT Solutions</h3><p>Dipisicing elit eiusmod temptext<br>of the printing and typesetting dunt</p><span class="read-more">READ MORE</span></div>
      </div>
      <div class="service">
        <div class="service-icon"><svg width="32" height="32" viewBox="0 0 32 32" fill="#fff"><ellipse cx="10" cy="7" rx="7" ry="3"/><rect x="3" y="8" width="14" height="6"/><rect x="3" y="16" width="14" height="6"/><rect x="3" y="24" width="14" height="5"/><path d="M20 10h8v4h-8zM20 20h8v4h-8z"/></svg></div>
        <div><h3>Database Management</h3><p>Dipisicing elit eiusmod temptext<br>of the printing and typesetting dunt</p><span class="read-more">READ MORE</span></div>
      </div>
      <div class="service">
        <div class="service-icon"><svg width="34" height="32" viewBox="0 0 34 32" fill="#fff"><circle cx="12" cy="10" r="6"/><path d="M1 30c0-8 5-12 11-12s11 4 11 12z"/><circle cx="24" cy="8" r="5"/><path d="M24 16c5 0 9 3 9 11h-8c0-4-1-8-4-10z"/></svg></div>
        <div><h3>IT Partners</h3><p>Dipisicing elit eiusmod temptext<br>of the printing and typesetting dunt</p><span class="read-more">READ MORE</span></div>
      </div>
      <div class="service">
        <div class="service-icon"><svg width="32" height="32" viewBox="0 0 32 32" fill="none" stroke="#fff" stroke-width="2"><rect x="3" y="4" width="26" height="24"/><path d="M3 10h26M7 15h8v8H7zM19 15h6M19 19h6M19 23h6"/></svg></div>
        <div><h3>Web Development</h3><p>Dipisicing elit eiusmod temptext<br>of the printing and typesetting dunt</p><span class="read-more">READ MORE</span></div>
      </div>
      <div class="service">
        <div class="service-icon"><svg width="32" height="32" viewBox="0 0 32 32" fill="#fff"><circle cx="11" cy="18" r="8"/><circle cx="24" cy="9" r="6"/><circle cx="11" cy="18" r="3" fill="#0d4a66"/><circle cx="24" cy="9" r="2" fill="#0d4a66"/></svg></div>
        <div><h3>Technical Support</h3><p>Dipisicing elit eiusmod temptext<br>of the printing and typesetting dunt</p><span class="read-more">READ MORE</span></div>
      </div>
      <div class="service">
        <div class="service-icon"><svg width="36" height="36" viewBox="0 0 36 36"><circle cx="18" cy="18" r="15" fill="none" stroke="#fff" stroke-width="3"/><text x="18" y="23" text-anchor="middle" font-family="Open Sans,sans-serif" font-weight="700" font-size="13" fill="#fff">24</text></svg></div>
        <div><h3>Premium Services</h3><p>Dipisicing elit eiusmod temptext<br>of the printing and typesetting dunt</p><span class="read-more">READ MORE</span></div>
      </div>
    </div>
  </div>
</section>

<section class="works">
  <div class="wrap">
    <h2 class="section-title">Our Recent Works</h2>
    <div class="work-grid">
      <div class="work"><div class="work-thumb" role="img" aria-label="Collage of travel photos spread across a surface" style="background:linear-gradient(135deg,#8fb0c8,#b5473e 55%,#d9d2c8)"></div><h3>IMAGE FORMAT</h3><p>Lorem Ipsum is simply dummy text<br>of the printing and typesetting</p><span class="btn-more">More</span></div>
      <div class="work"><div class="work-thumb" role="img" aria-label="Businessman holding a phone with floating squares" style="background:linear-gradient(90deg,#3a3a3a,#9a9a9a 60%,#dcdcdc)"></div><h3>SLIDESHOW FORMAT</h3><p>Lorem Ipsum is simply dummy text<br>of the printing and typesetting</p><span class="btn-more">More</span></div>
      <div class="work"><div class="work-thumb" role="img" aria-label="Woman holding a globe in her hand" style="background:linear-gradient(90deg,#f2ede8,#e6d2c0 50%,#4f7fa8)"></div><h3>GALLERY FORMAT</h3><p>Lorem Ipsum is simply dummy text<br>of the printing and typesetting</p><span class="btn-more">More</span></div>
      <div class="work"><div class="work-thumb" role="img" aria-label="Man pointing at a row of web page screens" style="background:linear-gradient(90deg,#6a9fd8,#e8e2b0 50%,#4d6fb5)"></div><h3>VIDEO FORMAT</h3><p>Lorem Ipsum is simply dummy text<br>of the printing and typesetting</p><span class="btn-more">More</span></div>
    </div>
  </div>
</section>

<section class="testimonials">
  <div class="wrap">
    <h2 class="section-title">TESTIMONIALS</h2>
    <div class="quote-row">
      <div class="quote"><span class="quote-mark">“</span><p>It is a long established fact that a reader will be distracted by the readable content of a page when looking at its layout. The point of using Lorem Ipsum is that it has a more-or-less normal distribution of</p>
        <div class="author"><div class="author-photo" role="img" aria-label="Client portrait"></div><div><div class="author-name">Declan</div><div class="author-co">Tallowmere Co.</div></div></div></div>
      <div class="quote"><span class="quote-mark">“</span><p>It is a long established fact that a reader will be distracted by the readable content of a page when looking at its layout. The point of using Lorem Ipsum is that it has a more-or-less normal distribution of</p>
        <div class="author"><div class="author-photo" role="img" aria-label="Client portrait"></div><div><div class="author-name">Marlo</div><div class="author-co">Tallowmere Co.</div></div></div></div>
    </div>
  </div>
</section>

<footer class="site-footer">
  <div class="wrap footer-cols">
    <div class="fcol" style="left:6px"><h4>Quick Links</h4>
      <div class="links-two"><ul><li>Home</li><li>Stories</li><li>Features</li><li>Contact</li></ul><ul><li>Sign In</li><li>Sign Up</li><li>Introduction</li><li>How to use the App</li></ul></div></div>
    <div class="fcol" style="left:283px"><h4>Company</h4><ul><li>Terms</li><li>Privacy</li><li>Contact Us</li></ul></div>
    <div class="fcol" style="left:491px"><h4>Connect With Us</h4><ul><li>Friendwall</li><li>Chirper</li><li>WorkLinks</li></ul></div>
    <div class="fcol" style="left:726px"><h4>Contact Us</h4>
      <div class="field">Name</div><div class="field">Mail</div><div class="field msg">Message</div><span class="submit">SUBMIT</span></div>
  </div>
</footer>
<div class="bottom-bar">
  <div class="wrap">
    <span class="copy">© 2014 northpierweb.com. All rights reserved.</span>
    <div class="social" aria-label="Social links"><span></span><span></span><span></span><span></span><span></span><span></span><span></span></div>
  </div>
</div>
</body>
</html>
```